Business Cards Design for the electrical wholesaler: clean bold dynamic :)

We need a business card design that would follow our latest brand guidelines. As an electrical wholesaler we want to bring a fresh look and feel into the industry. The design should be clean bold and dynamic. It should come alive with the renewed energy of our green colour. Our grey colour should keep things balanced and complement the notion of maturity and responsibility. We employ Lato as a corporate font however are not bound by this font and we’re open to interpretation here.

Target Market(s)

Electrical contractors

Industry/Entity Type

Business

Contact Information for Business Card

Logo
Name & Surname: Halyna Dorosh
Job Title: Director of Marketing
Email: halya.dorosh@quillmail.example
Cell phone: XXX.XXX.XXXX
Address: 20517 - 87 Ave. Edmonton, AB, Canada. T6K 4N8
Business Phone: 780.555.0184
Website: www.brovix.example

Font styles to use
Other font styles liked:
• Lato

Requirements
Must have
• Logo & website
Nice to have
• Brand elements - some of them you may find in the attached Brand Guidelines (e.g. three lines on the background signifying "W")

```html
<!DOCTYPE html>
<html lang="en">
<head>
<meta charset="utf-8">
<title>Brovix Business Card</title>
<link rel="stylesheet" href="https://fonts.googleapis.com/css2?family=Exo+2:wght@500&family=Roboto:wght@400;500&display=swap">
<style>
  :root {
    --backdrop: #e9e4dd;
    --card: #f7f7f5;
    --card-edge: #d9d9d5;
    --green: #7cbf2e;
    --grey: #4a4c4e;
    --grey-soft: #5a5c5e;
    --icon-ring: #8ab04a;
  }
  html, body {
    margin: 0;
    width: 1200px;
    height: 1054px;
    overflow: hidden;
    background: var(--backdrop);
  }
  .card {
    position: absolute;
    left: 172px;
    top: 269px;
    width: 855px;
    height: 516px;
    background: var(--card);
    border: 1px solid var(--card-edge);
    overflow: hidden;
    font-family: "Roboto", Arial, sans-serif;
    color: var(--grey-soft);
  }
  .card__accent {
    position: absolute;
    left: 0;
    top: 0;
  }
  .brand {
    position: absolute;
    left: 38px;
    top: 42px;
    display: flex;
    align-items: center;
    gap: 12px;
  }
  .brand__dot {
    width: 40px;
    height: 40px;
    border-radius: 50%;
    background: var(--green);
  }
  .brand__name {
    font-family: "Roboto", Arial, sans-serif;
    font-weight: 500;
    font-size: 52px;
    line-height: 1;
    color: var(--grey);
  }
  .person {
    position: absolute;
    left: 40px;
    top: 228px;
  }
  .person__name {
    margin: 0;
    font-family: "Exo 2", Arial, sans-serif;
    font-weight: 500;
    font-size: 33px;
    line-height: 1.1;
    color: var(--green);
  }
  .person__role {
    margin: 4px 0 0;
    font-size: 20px;
    color: var(--grey-soft);
  }
  .address {
    position: absolute;
    left: 40px;
    top: 315px;
    margin: 0;
    font-style: normal;
    font-size: 21px;
    line-height: 29px;
    color: var(--grey-soft);
  }
  .contacts {
    position: absolute;
    left: 40px;
    top: 392px;
    margin: 0;
    padding: 0;
    list-style: none;
    font-size: 21px;
    line-height: 29px;
  }
  .contacts__item {
    display: flex;
    align-items: center;
    gap: 14px;
  }
  .contacts__icon {
    width: 20px;
    height: 20px;
    flex: none;
  }
</style>
</head>
<body>
  <section class="card">
    <svg class="card__accent" width="855" height="516" viewBox="0 0 855 516" aria-hidden="true">
      <circle cx="630" cy="266" r="200" fill="var(--grey)" opacity="0.92"/>
    </svg>

    <div class="brand">
      <span class="brand__dot"></span>
      <span class="brand__name">brovix</span>
    </div>

    <div class="person">
      <h1 class="person__name">Halyna Dorosh</h1>
      <p class="person__role">Director of Marketing</p>
    </div>

    <address class="address">20517 - 87 Ave. Edmonton,<br>AB, Canada T6K 4N8</address>

    <ul class="contacts">
      <li class="contacts__item">
        <svg class="contacts__icon" viewBox="0 0 20 20" aria-hidden="true">
          <circle cx="10" cy="10" r="9" fill="none" stroke="var(--icon-ring)" stroke-width="1.5"/>
          <path d="M6.5 6.5c0 4 3 7 7 7l0.8-1.8-2-1-1 1c-1.2-.5-2.5-1.8-3-3l1-1-1-2z" fill="var(--icon-ring)"/>
        </svg>
        <span>+1 780.555.0184</span>
      </li>
      <li class="contacts__item">
        <svg class="contacts__icon" viewBox="0 0 20 20" aria-hidden="true">
          <circle cx="10" cy="10" r="9" fill="none" stroke="var(--icon-ring)" stroke-width="1.5"/>
          <rect x="5.5" y="7" width="9" height="6.5" fill="none" stroke="var(--icon-ring)" stroke-width="1.2"/>
          <path d="M5.5 7l4.5 3.5 4.5-3.5" fill="none" stroke="var(--icon-ring)" stroke-width="1.2"/>
        </svg>
        <span>halya.dorosh@quillmail.example</span>
      </li>
      <li class="contacts__item">
        <svg class="contacts__icon" viewBox="0 0 20 20" aria-hidden="true">
          <circle cx="10" cy="10" r="9" fill="none" stroke="var(--icon-ring)" stroke-width="1.5"/>
          <circle cx="10" cy="10" r="4.8" fill="none" stroke="var(--icon-ring)" stroke-width="1.1"/>
          <path d="M5.2 10h9.6M10 5.2c-2 2.6-2 7 0 9.6M10 5.2c2 2.6 2 7 0 9.6" fill="none" stroke="var(--icon-ring)" stroke-width="1"/>
        </svg>
        <span>www.brovix.example</span>
      </li>
    </ul>
  </section>
</body>
</html>
```